New Banner Ad Design Project

We are a start-up in San Francisco that sells consignment clothes with a percentage of the proceeds donated to charity. Also, volunteer groups can conduct dress drives and send them to us and we will sell them and give their charity back 60% of the proceeds.

We have several uses for banners:
- Home page banner:
- Promote timely Flash Sales (they last only 96 hours) which happen 2x/week
- Promote how good it feels to give back and shop
- Promote any special promotions such as a Gift With Purchase
- Community banner:
- Promote the lifestyle
- Promote any particular group conducting a dress drive

If you are going to submit one banner it is to be for an upcoming sale, as the two attached files address (maternity sale). If we find the right designer we will consider working with them beyond the design contest for future sale banners as well as others

We consider our 'competitors' to be The Garment Venture, The TrueCloset, WeavTurn, KnitRise, WearAgain. Our key differentiator is the charitable components and how groups are conducting dress drives to raise money.

We are in the midst of changing our company name, tagline and logo. The new company will be called 'LunaTessa' and our tagline is 'Rewoven Kindness'

Target Market(s)

Our initial audience is young women 16 - 30. We will be focusing on Prom February through May which appeals to 16 - 18 year olds.

We also have maternity-wear. We want these women to feel fashionable

We are focused on individuals who want to give back.

Industry/Entity Type

Charity

Font styles to use
Serif
Sans Serif

Colors
8769ae
1b1b1b
474747
c3c3c3
86cfc6
b7a5cd

Requirements
Must have
• - Youthful and stylish voice (not to be confused with Young)
- Appealing visuals
- Powerful call-to-action as it pertains to banners for our flash sales
- An inclusive feel
- Communicates our charitable component
Nice to have
• - Emotional appeal
- Women wearing our clothes (see attached)
Should not have
• - Too much text
- Too girly; overly flowery

```html
<!DOCTYPE html>
<html lang="en">
<head>
<meta charset="utf-8">
<title>Maternity Sale Banner</title>
<link rel="stylesheet" href="https://fonts.googleapis.com/css2?family=Raleway:wght@200;300&family=Montserrat:wght@800&display=swap">
<style>
  :root {
    --sky: #7b9cbc;
    --white: #ffffff;
    --plum: #5c3d72;
    --cream: #fbf7f1;
    --linen: #f6ebe0;
    --blush: #efcfbd;
    --rose: #e6b8a3;
  }
  html, body {
    margin: 0;
    padding: 0;
    width: 1200px;
    height: 553px;
    overflow: hidden;
    background: var(--sky);
  }
  .banner {
    display: block;
    width: 1200px;
    height: 553px;
  }
  .headline-top {
    font-family: "Raleway", sans-serif;
    font-weight: 200;
    font-size: 130px;
    fill: var(--white);
  }
  .headline-sale {
    font-family: "Montserrat", sans-serif;
    font-weight: 800;
    font-size: 318px;
  }
  .cta-disc { fill: var(--plum); }
  .cta-label {
    font-family: "Raleway", sans-serif;
    font-weight: 300;
    font-size: 38px;
    fill: var(--white);
  }
  .cta-bag { fill: var(--white); }
  .cta-handle { fill: none; stroke: var(--white); stroke-width: 2; }
</style>
</head>
<body>
<svg class="banner" viewBox="0 0 1200 553" xmlns="http://www.w3.org/2000/svg">
  <defs>
    <linearGradient id="photo-tones" x1="0" y1="0" x2="1" y2="0.35">
      <stop offset="0" stop-color="var(--cream)"/>
      <stop offset="0.22" stop-color="var(--linen)"/>
      <stop offset="0.42" stop-color="var(--blush)"/>
      <stop offset="0.55" stop-color="var(--rose)"/>
      <stop offset="0.7" stop-color="var(--blush)"/>
      <stop offset="0.85" stop-color="var(--linen)"/>
      <stop offset="1" stop-color="var(--cream)"/>
    </linearGradient>
    <filter id="letter-lift" x="-5%" y="-5%" width="110%" height="115%">
      <feDropShadow dx="0" dy="2" stdDeviation="2" flood-color="#3d5570" flood-opacity="0.25"/>
    </filter>
  </defs>

  <rect class="backdrop" width="1200" height="553" fill="var(--sky)"/>

  <text class="headline-top" x="85" y="192" textLength="780" lengthAdjust="spacingAndGlyphs">MATERNITY</text>

  <g role="img" aria-label="Photo of an expectant mother in sunglasses showing through the letters" filter="url(#letter-lift)">
    <text class="headline-sale" x="78" y="455" textLength="778" lengthAdjust="spacingAndGlyphs" fill="url(#photo-tones)">SALE</text>
  </g>

  <g class="cta">
    <circle class="cta-disc" cx="1033" cy="284" r="133"/>
    <text class="cta-label" x="1035" y="278" text-anchor="middle" textLength="213" lengthAdjust="spacingAndGlyphs">SHOP NOW</text>
    <g class="cta-icon">
      <path class="cta-handle" d="M1019 306 C1019 286 1046 286 1046 306"/>
      <path class="cta-bag" d="M1010 300 L1055 297 L1061 362 L1006 363 Z"/>
    </g>
  </g>
</svg>
</body>
</html>
```